Business Card Design for Technology Company

New business card design needed for technology company director.
Ideally, the design will fit the style and nature of the industry. We are a supplier of quality products and services, and we hope the design will give customers and suppliers this impression.

Target Market(s)

3D Printing Industry

Industry/Entity Type

Technology Equipment

Contact Information for Business Card

Name: Marcus Lin
Title: Director
Company address: Factory K4, 7B Harlowe Road, Springvale Victoria Australia 3150
Telephone: +61-3-8555 6413
Email: marcus.lin@vortalmake.com.au
Website: www.vortalmake.com.au

Requirements
Must have
• All information in business card details
• Company logo
• '3D Printers and 3D Print Filaments' at proper place
Nice to have
• Style to fit the industry
• Colour to fit logo

```html
<!DOCTYPE html>
<html lang="en">
<head>
<meta charset="utf-8">
<title>Vortalmake – Business Card</title>
<link href="https://fonts.googleapis.com/css2?family=Arimo:wght@400;700&display=swap" rel="stylesheet">
<style>
  :root {
    --page-bg: #e9ebee;
    --card-white: #ffffff;
    --ink: #1a1a1a;
    --navy-deep: #1c1a5e;
    --navy-mid: #263b8f;
    --blue-bright: #1f8fd8;
    --orange: #f7941d;
    --orange-deep: #e8621b;
    --contact-text: #ffffff;
    --shadow: rgba(20, 30, 60, 0.18);
  }
  * { box-sizing: border-box; margin: 0; padding: 0; }
  html, body {
    width: 1200px; height: 900px; overflow: hidden;
    background: var(--page-bg);
    font-family: "Arimo", Arial, sans-serif;
  }
  .sheet {
    width: 1200px; height: 900px;
    display: flex; align-items: center; justify-content: center; gap: 60px;
  }
  .card {
    position: relative;
    width: 520px; height: 318px;
    background: var(--card-white);
    box-shadow: 0 14px 30px var(--shadow), 0 2px 4px var(--shadow);
    overflow: hidden;
  }

  /* Front */
  .card-front {
    display: flex; align-items: center; justify-content: center; gap: 22px;
  }
  .brand-square {
    width: 70px; height: 70px; flex: none;
    background: var(--blue-bright);
  }
  .brand-lockup { display: flex; flex-direction: column; }
  .brand-name {
    font-size: 44px; font-weight: 700; letter-spacing: 3px; line-height: 1;
    color: var(--ink);
  }
  .brand-tagline {
    margin-top: 8px;
    font-size: 10.5px; font-weight: 400; letter-spacing: 1.6px;
    text-transform: uppercase; white-space: nowrap;
    color: var(--ink);
  }

  /* Back */
  .card-back .identity {
    position: absolute; left: 30px; top: 24px;
  }
  .brand-name-small {
    font-size: 26px; font-weight: 700; letter-spacing: 2px; line-height: 1;
    color: var(--ink);
  }
  .brand-tagline-small {
    margin-top: 5px;
    font-size: 8px; letter-spacing: 1px;
    text-transform: uppercase; white-space: nowrap;
    color: var(--ink);
  }
  .person {
    position: relative; margin-top: 14px; padding-left: 18px;
  }
  .person::before {
    content: ""; position: absolute; left: 0; top: 4px;
    border-left: 10px solid var(--orange-deep);
    border-top: 8px solid transparent; border-bottom: 8px solid transparent;
  }
  .person-name { font-size: 18px; font-weight: 700; color: var(--ink); line-height: 1.2; }
  .person-title { font-size: 16px; color: var(--ink); line-height: 1.2; }

  .band-edge, .contact-band {
    position: absolute; left: 0; right: 0; bottom: 0; height: 190px;
    clip-path: polygon(0 40px, 100% 0, 100% 100%, 0 100%);
  }
  .band-edge {
    height: 194px;
    background: var(--orange);
  }
  .contact-band {
    background: linear-gradient(100deg, var(--navy-deep), var(--navy-mid) 70%, var(--blue-bright));
    padding: 54px 30px 0 40px;
    color: var(--contact-text);
    font-size: 14px; line-height: 1.4;
  }
  .address { margin-bottom: 8px; }
  .contact-line { display: flex; align-items: center; gap: 8px; }
  .contact-line svg { width: 13px; height: 13px; fill: var(--contact-text); flex: none; }
  .website { margin-top: 6px; }
</style>
</head>
<body>
<main class="sheet">
  <section class="card card-front" aria-label="Card front">
    <div class="brand-square" aria-hidden="true"></div>
    <div class="brand-lockup">
      <div class="brand-name">VORTALMAKE</div>
      <div class="brand-tagline">3D Printers and 3D Print Filaments</div>
    </div>
  </section>

  <section class="card card-back" aria-label="Card back">
    <div class="identity">
      <div class="brand-name-small">VORTALMAKE</div>
      <div class="brand-tagline-small">3D Printers and 3D Print Filaments</div>
      <div class="person">
        <div class="person-name">Marcus Lin</div>
        <div class="person-title">Director</div>
      </div>
    </div>
    <div class="band-edge" aria-hidden="true"></div>
    <div class="contact-band">
      <p class="address">Factory K4, 7B Harlowe Road<br>Springvale Victoria Australia 3150</p>
      <p class="contact-line">
        <svg viewBox="0 0 16 16" aria-hidden="true"><path d="M3 1h3l1.5 4-2 1.2a9 9 0 0 0 4.3 4.3L11 8.5l4 1.5v3a2 2 0 0 1-2 2A12 12 0 0 1 1 3a2 2 0 0 1 2-2z"/></svg>
        +61-3-8555 6413
      </p>
      <p class="contact-line">
        <svg viewBox="0 0 16 16" aria-hidden="true"><path d="M1 3h14v10H1z M2 4.2v.3l6 4 6-4v-.3z" fill-rule="evenodd"/></svg>
        marcus.lin@vortalmake.com.au
      </p>
      <p class="website">www.vortalmake.com.au</p>
    </div>
  </section>
</main>
</body>
</html>
```